Accounting firm needing business card / letterhead designed
Marcus L. Trenholm, CPA
marcus@veltrowledger.com
www.veltrowledger.com
842 E Alder Ave Perrysburg, OH 43827
419-562-0974

```html
<!DOCTYPE html>
<html lang="en">
<head>
<meta charset="utf-8">
<title>Veltrow Ledger – Business Card</title>
<link rel="stylesheet" href="https://fonts.googleapis.com/css2?family=Lato:wght@400;700&display=swap">
<style>
  :root {
    --page-bg: #efefef;
    --card-dark: #3b3b3b;
    --card-dark-deep: #2f2f2f;
    --card-light: #ffffff;
    --navy: #27215e;
    --green: #8dc63f;
    --ink: #1e1e1e;
    --white: #ffffff;
  }
  * { box-sizing: border-box; margin: 0; padding: 0; }
  html, body {
    width: 1200px;
    height: 586px;
    overflow: hidden;
    background: var(--page-bg);
    font-family: "Lato", sans-serif;
  }
  .canvas {
    position: relative;
    width: 1200px;
    height: 586px;
  }
  .card {
    position: absolute;
    top: 129px;
    width: 501px;
    height: 300px;
    overflow: hidden;
  }
  /* Front side */
  .card--front {
    left: 61px;
    color: var(--white);
  }
  .card__texture {
    position: absolute;
    inset: 0;
    background: linear-gradient(135deg, var(--card-dark) 0%, var(--card-dark-deep) 50%, var(--card-dark) 100%);
  }
  .front__brand {
    position: absolute;
    left: 0;
    right: 0;
    top: 118px;
    text-align: center;
    font-weight: 700;
    font-size: 38px;
    letter-spacing: 5px;
    color: var(--white);
  }
  .front__url {
    position: absolute;
    left: 0;
    right: 0;
    top: 254px;
    text-align: center;
    font-weight: 700;
    font-size: 11.5px;
    letter-spacing: 2.6px;
    color: var(--white);
  }
  /* Back side */
  .card--back {
    left: 619px;
    background: var(--card-light);
  }
  .back__brand {
    position: absolute;
    left: 0;
    right: 0;
    top: 66px;
    text-align: center;
    font-weight: 700;
    font-size: 30px;
    letter-spacing: 4px;
    color: var(--navy);
  }
  .contact-list {
    position: absolute;
    left: 28px;
    top: 198px;
    list-style: none;
  }
  .contact-list__item {
    display: flex;
    align-items: center;
    height: 25px;
    font-size: 11.5px;
    color: var(--ink);
  }
  .contact-list__icon {
    width: 18px;
    height: 18px;
    margin-right: 6px;
    flex: none;
  }
  .holder {
    position: absolute;
    right: 30px;
    top: 218px;
    text-align: right;
  }
  .holder__name {
    font-weight: 700;
    font-size: 16.5px;
    color: var(--navy);
  }
  .holder__title {
    font-size: 10.5px;
    color: var(--ink);
    margin-top: 1px;
  }
  .base-band {
    position: absolute;
    left: 0;
    bottom: 0;
    width: 502px;
    height: 14px;
  }
</style>
</head>
<body>
<main class="canvas">

  <section class="card card--front">
    <div class="card__texture" role="img" aria-label="Dark grey low-poly faceted background texture"></div>
    <div class="front__brand">VELTROW LEDGER</div>
    <div class="front__url">www.veltrowledger.com</div>
  </section>

  <section class="card card--back">
    <div class="back__brand">VELTROW LEDGER</div>

    <ul class="contact-list">
      <li class="contact-list__item">
        <svg class="contact-list__icon" viewBox="0 0 18 18" aria-hidden="true">
          <circle cx="9" cy="9" r="9" fill="var(--navy)"/>
          <path d="M4.5 8.2c0-1.6 2-2.4 4.5-2.4s4.5.8 4.5 2.4l-1.6.5-.4-1.2c-.8-.3-4.2-.3-5 0l-.4 1.2z" fill="var(--white)"/>
          <path d="M6.2 9h5.6l.9 3.6H5.3z" fill="var(--white)"/>
        </svg>
        419-562-0974
      </li>
      <li class="contact-list__item">
        <svg class="contact-list__icon" viewBox="0 0 18 18" aria-hidden="true">
          <circle cx="9" cy="9" r="9" fill="var(--navy)"/>
          <rect x="4.5" y="5.8" width="9" height="6.4" fill="none" stroke="var(--white)" stroke-width="1"/>
          <path d="M4.5 5.8 9 9.6l4.5-3.8" fill="none" stroke="var(--white)" stroke-width="1"/>
        </svg>
        marcus@veltrowledger.com
      </li>
      <li class="contact-list__item">
        <svg class="contact-list__icon" viewBox="0 0 18 18" aria-hidden="true">
          <circle cx="9" cy="9" r="9" fill="var(--navy)"/>
          <rect x="6" y="4" width="6" height="10" fill="var(--white)"/>
          <path d="M7.2 5.5h1.2M9.6 5.5h1.2M7.2 7.5h1.2M9.6 7.5h1.2M7.2 9.5h1.2M9.6 9.5h1.2" stroke="var(--navy)" stroke-width="0.9"/>
          <rect x="8.3" y="11.5" width="1.4" height="2.5" fill="var(--navy)"/>
        </svg>
        842 E Alder Ave Perrysburg, OH 43827
      </li>
    </ul>

    <div class="holder">
      <div class="holder__name">Marcus L. Trenholm</div>
      <div class="holder__title">CPA</div>
    </div>

    <svg class="base-band" viewBox="0 0 502 14" aria-hidden="true">
      <rect x="0" y="3" width="312" height="11" fill="var(--green)"/>
      <path d="M302 14C308 4 314 0 328 0H502V14Z" fill="var(--navy)"/>
      <path d="M302 14C308 4 314 0 328 0" fill="none" stroke="var(--white)" stroke-width="3"/>
    </svg>
  </section>

</main>
</body>
</html>
```